Creation of a construction/bricklaying business website

Following the template format of "Halloway 7", the following content would need to be included:
1. Landing page with 3 tiles that go to their own pages.
- Landing page to include background photo and description of services offered.
2. 3 tiles to include:
a) "Contact Us For A Free Quote or Friendly Discussion" Form (middle tile)
b) Case Studies and Testimonials
c) Certifications and Professional Membership
- Design logo to be used from previous SketchNestle project. Example of logo attached below, please access full JPG files from our account.

Target Market(s)

Prospective clients seeking construction work (bricklaying speciality)

Industry/Entity Type

Residential Construction

Coding

Coded - Design and coding required

Number of Pages Required

4 page

Font styles to use
Sans Serif

Colors

Designer to choose colors to be used in the design.

Requirements
Must have
• Following the template format of "Halloway 7", the following content would need to be included:
• 1. Landing parent page with 3 tiles that go to the 3 child pages.
• - Landing page to include background photo and description of services offered.
• 2. 3 tiles to include:
• a) "Contact Us For A Free Quote or Friendly Discussion" Form (middle tile)
• b) Case Studies and Testimonials (first tile / left side)
• c) Certifications and Professional Memberships (third tile / right side) (This should include logos of the relevant organisations being displayed. Specifically GQT and the Pillar Seal GQT).
• - Design logo to be used from previous SketchNestle project. Example of logo attached below, please access full JPG files from our account.
Nice to have
• Sleek and modern feel.
• Approachable in terms of how people can contact the company for a quote.
• Traditional pictures to give credibility and comfort around choosing this company.
Should not have
• Cheesy pictures
• Over-complicated
• Simple to use
• Easy URL domain name

```html
<!DOCTYPE html>
<html lang="en">
<head>
<meta charset="utf-8">
<title>R.T.Marlow Construction Ltd</title>
<link rel="stylesheet" href="https://fonts.googleapis.com/css2?family=Jost:wght@400;500&family=Saira:wght@500;600&display=swap">
<style>
  :root {
    --blue: #0d4fa8;
    --blue-dark: #0a3f86;
    --ink: #1b1b1b;
    --grey-text: #333;
    --tile-bg: #e8eceb;
    --footer-bg: #000;
    --white: #fff;
    --hero-top: #6b6966;
    --hero-bottom: #4a4946;
  }
  * { box-sizing: border-box; margin: 0; padding: 0; }
  html, body { width: 986px; height: 1200px; overflow: hidden; background: var(--white); }
  body { position: relative; font-family: "Jost", sans-serif; color: var(--ink); }

  .hero {
    position: absolute; left: 0; top: 0; width: 986px; height: 481px;
    background: linear-gradient(160deg, #7b7873 0%, var(--hero-top) 40%, var(--hero-bottom) 100%);
  }
  .top-contact { position: absolute; top: 16px; display: flex; align-items: center; gap: 7px; color: var(--white); font-size: 12px; line-height: 18px; }
  .top-contact.phone { left: 133px; }
  .top-contact.email { left: 671px; }
  .round-icon { width: 31px; height: 31px; border-radius: 50%; background: var(--blue); display: flex; align-items: center; justify-content: center; flex-shrink: 0; }

  .brand { position: absolute; left: 0; width: 986px; top: 140px; text-align: center; }
  .brand-name { font-family: "Saira", sans-serif; font-weight: 600; font-size: 50px; color: var(--blue); letter-spacing: -1px; line-height: 56px; }
  .hero-title { position: absolute; top: 232px; left: 0; width: 986px; text-align: center; font-family: "Saira", sans-serif; font-weight: 500; font-size: 22px; line-height: 26px; color: var(--white); }
  .cta { position: absolute; left: 426px; top: 310px; width: 133px; height: 27px; background: var(--blue); color: var(--white); font-size: 13px; display: flex; align-items: center; justify-content: center; gap: 6px; }

  .service { position: absolute; top: 436px; width: 130px; text-align: center; }
  .service-badge { width: 84px; height: 84px; margin: 0 auto; border-radius: 50%; border: 3px solid var(--blue-dark); background: radial-gradient(circle at 50% 40%, #fff 0%, #e4e4e4 100%); display: flex; align-items: center; justify-content: center; }
  .service-shadow { width: 60px; height: 4px; margin: 6px auto 0; border-radius: 50%; background: rgba(0,0,0,.08); }
  .service-name { margin-top: 12px; font-family: "Saira", sans-serif; font-weight: 500; font-size: 16px; line-height: 18px; color: #2a2a2a; }

  .intro { position: absolute; top: 611px; left: 135px; width: 716px; text-align: center; font-size: 13px; line-height: 20px; }
  .intro p + p { margin-top: 13px; }

  .tile { position: absolute; top: 726px; width: 240px; height: 224px; padding-top: 22px; text-align: center; }
  .tile.shaded { background: var(--tile-bg); }
  .tile-art { height: 55px; display: flex; justify-content: center; align-items: center; gap: 3px; }
  .tile-title { margin-top: 12px; font-family: "Saira", sans-serif; font-weight: 500; font-size: 12px; line-height: 15px; }
  .tile-text { margin: 11px 6px 0; font-size: 11.5px; line-height: 17.5px; color: var(--grey-text); }
  .tile-link { display: inline-block; margin-top: 10px; font-family: "Saira", sans-serif; font-weight: 500; font-size: 12px; color: var(--blue); text-decoration: underline; }

  .footer { position: absolute; left: 0; top: 994px; width: 986px; height: 206px; background: var(--footer-bg); color: var(--white); }
  .footer-brand { position: absolute; top: 30px; width: 986px; text-align: center; font-family: "Saira", sans-serif; font-weight: 600; font-size: 20px; color: var(--blue); }
  .footer-contact { position: absolute; top: 88px; display: flex; align-items: center; gap: 9px; font-size: 11.5px; line-height: 18px; }
  .footer-rule { position: absolute; top: 139px; left: 156px; width: 676px; height: 1px; background: #13233d; }
  .copyright { position: absolute; top: 162px; left: 157px; font-size: 11.5px; }
  .social { position: absolute; top: 155px; left: 709px; display: flex; gap: 4px; }
  .social span { width: 25px; height: 25px; border-radius: 50%; background: var(--white); }
</style>
</head>
<body>
  <section class="hero" role="img" aria-label="Background photograph of a builder plastering a block wall">
  </section>

  <div class="top-contact phone">
    <span class="round-icon"><svg width="14" height="14" viewBox="0 0 24 24"><path fill="#fff" d="M6.6 10.8a15 15 0 0 0 6.6 6.6l2.2-2.2c.3-.3.7-.4 1-.2 1.1.4 2.3.6 3.6.6.6 0 1 .4 1 1V20c0 .6-.4 1-1 1A17 17 0 0 1 3 4c0-.6.4-1 1-1h3.5c.6 0 1 .4 1 1 0 1.3.2 2.5.6 3.6.1.3 0 .7-.2 1z"/></svg></span>
    <span>Call Us On<br>555.010.2468</span>
  </div>
  <div class="top-contact email">
    <span class="round-icon"><svg width="15" height="12" viewBox="0 0 20 14"><rect x="1" y="1" width="18" height="12" fill="none" stroke="#fff" stroke-width="1.6"/><path d="M1 1l9 7 9-7" fill="none" stroke="#fff" stroke-width="1.6"/></svg></span>
    <span>Email Us On<br>info@rtmarlowbuild.com</span>
  </div>

  <div class="brand"><div class="brand-name">R.T.Marlow Construction Ltd</div></div>

  <h1 class="hero-title">R.T.Marlow Construction Ltd is a construction company that<br>has expertise and experience in the following areas</h1>
  <div class="cta">Contact Us Today <span>&rarr;</span></div>

  <div class="service" style="left:109px">
    <div class="service-badge"><svg width="44" height="40" viewBox="0 0 44 40" fill="none" stroke="#333" stroke-width="2"><path d="M4 18L18 6l14 12"/><path d="M8 15v17h20V15"/><rect x="12" y="21" width="8" height="6"/><path d="M26 12h10v20h-8"/><path d="M6 37h32"/></svg></div>
    <div class="service-shadow"></div><div class="service-name">Extensions</div>
  </div>
  <div class="service" style="left:236px">
    <div class="service-badge"><svg width="46" height="40" viewBox="0 0 46 40"><path d="M3 20L23 4l20 16" fill="none" stroke="#333" stroke-width="3"/><path d="M9 17v20h28V17L23 7z" fill="#333"/><rect x="14" y="20" width="4" height="4" fill="#fff"/><rect x="20" y="20" width="4" height="4" fill="#fff"/><rect x="14" y="26" width="4" height="4" fill="#fff"/><rect x="20" y="26" width="4" height="4" fill="#fff"/><rect x="28" y="25" width="5" height="12" fill="#fff"/><rect x="32" y="6" width="4" height="8" fill="#333"/></svg></div>
    <div class="service-shadow"></div><div class="service-name">New build /<br>New houses</div>
  </div>
  <div class="service" style="left:370px">
    <div class="service-badge"><svg width="50" height="36" viewBox="0 0 50 36" fill="#333"><rect x="0" y="0" width="26" height="3"/><g><rect x="0" y="6" width="11" height="5"/><rect x="13" y="6" width="11" height="5"/><rect x="26" y="6" width="11" height="5"/><rect x="39" y="6" width="11" height="5"/><rect x="6" y="13" width="11" height="5"/><rect x="19" y="13" width="11" height="5"/><rect x="32" y="13" width="11" height="5"/><rect x="0" y="20" width="11" height="5"/><rect x="13" y="20" width="11" height="5"/><rect x="26" y="20" width="11" height="5"/><rect x="39" y="20" width="11" height="5"/><rect x="6" y="27" width="11" height="5"/><rect x="19" y="27" width="11" height="5"/><rect x="32" y="27" width="11" height="5"/></g></svg></div>
    <div class="service-shadow"></div><div class="service-name">Garden walls</div>
  </div>
  <div class="service" style="left:490px">
    <div class="service-badge"><svg width="46" height="40" viewBox="0 0 46 40" fill="none" stroke="#333" stroke-width="2"><rect x="2" y="4" width="12" height="7"/><rect x="14" y="4" width="12" height="7"/><rect x="8" y="11" width="12" height="7"/><rect x="2" y="18" width="12" height="7"/><rect x="8" y="25" width="12" height="7"/><rect x="2" y="32" width="12" height="6"/><path d="M22 20l14-10 6 8-14 10z" fill="#333"/><path d="M36 24l6 12"/></svg></div>
    <div class="service-shadow"></div><div class="service-name">Plastering</div>
  </div>
  <div class="service" style="left:617px">
    <div class="service-badge"><svg width="46" height="36" viewBox="0 0 46 36" fill="#333"><rect x="5" y="0" width="2" height="10"/><path d="M1 10h10l-5 12z"/><rect x="14" y="16" width="9" height="5"/><rect x="25" y="16" width="9" height="5"/><rect x="36" y="16" width="9" height="5"/><rect x="9" y="23" width="9" height="5"/><rect x="20" y="23" width="9" height="5"/><rect x="31" y="23" width="9" height="5"/><rect x="14" y="30" width="9" height="5"/><rect x="25" y="30" width="9" height="5"/></svg></div>
    <div class="service-shadow"></div><div class="service-name">Brickwork</div>
  </div>
  <div class="service" style="left:746px">
    <div class="service-badge"><svg width="46" height="40" viewBox="0 0 46 40" fill="#333"><path d="M4 2h12v3H12v5h-4V5H4z"/><rect x="8" y="10" width="4" height="14"/><path d="M4 22h12v10a6 6 0 0 1-12 0z"/><path d="M20 38l8-14 6 6 4-4 6 12z"/><circle cx="40" cy="30" r="2" fill="#fff"/></svg></div>
    <div class="service-shadow"></div><div class="service-name">Groundworks</div>
  </div>

  <div class="intro">
    <p>We pride ourselves on attention to detail, pride in our completed project and client satisfaction. We believe in full transparency and this is reflected in the jobs we quote for you. We break down each step with both labour and materials cost so you can see exactly what you are paying for.</p>
    <p>Feel free to get in touch and we can talk through what you are looking to achieve.</p>
  </div>

  <div class="tile shaded" style="left:133px">
    <div class="tile-art"><div role="img" aria-label="Case study illustration with speech bubble and document" style="width:76px;height:52px;background:linear-gradient(135deg,#2f5fa8,#4c5a6c);border-radius:4px"></div></div>
    <div class="tile-title">Case Studies and<br>Testimonials</div>
    <p class="tile-text">Ut wisi enim ad minim veniam, quis nostrud exerci tation ullamcorper suscipit lobortis nisl ut aliquip ex ea commodo consequat.</p>
    <a class="tile-link">Read More</a>
  </div>
  <div class="tile" style="left:373px">
    <div class="tile-art"><svg width="50" height="54" viewBox="0 0 50 54" fill="none" stroke="#0d4fa8" stroke-width="3"><path d="M10 2h26l10 10v40H10z"/><path d="M36 2v10h10"/><path d="M20 24h18M20 32h18M20 40h18"/><path d="M2 40l5 8 9-16" stroke="#333"/></svg></div>
    <div class="tile-title">Contact Us For A<br>Free Quote</div>
    <p class="tile-text">Ut wisi enim ad minim veniam, quis nostrud exerci tation ullamcorper suscipit lobortis nisl ut aliquip ex ea commodo consequat.</p>
    <a class="tile-link">Contact Us</a>
  </div>
  <div class="tile shaded" style="left:613px">
    <div class="tile-art">
      <div role="img" aria-label="GQT membership badge" style="width:30px;height:51px;background:#c8102e"></div>
      <div role="img" aria-label="Pillar Seal GQT badge" style="width:34px;height:51px;background:#b5121b"></div>
    </div>
    <div class="tile-title">Certifications and Professional<br>Memberships</div>
    <p class="tile-text">Ut wisi enim ad minim veniam, quis nostrud exerci tation ullamcorper suscipit lobortis nisl ut aliquip ex ea commodo consequat.</p>
    <a class="tile-link">Know More</a>
  </div>

  <footer class="footer">
    <div class="footer-brand">R.T.Marlow Construction Ltd</div>
    <div class="footer-contact" style="left:157px">
      <span class="round-icon"><svg width="12" height="16" viewBox="0 0 12 16"><path fill="#fff" d="M6 0a6 6 0 0 0-6 6c0 4.5 6 10 6 10s6-5.5 6-10a6 6 0 0 0-6-6zm0 8.2A2.2 2.2 0 1 1 6 3.8a2.2 2.2 0 0 1 0 4.4z"/></svg></span>
      <span>Street Name, City Name<br>State Zipcode</span>
    </div>
    <div class="footer-contact" style="left:421px">
      <span class="round-icon"><svg width="14" height="14" viewBox="0 0 24 24"><path fill="#fff" d="M6.6 10.8a15 15 0 0 0 6.6 6.6l2.2-2.2c.3-.3.7-.4 1-.2 1.1.4 2.3.6 3.6.6.6 0 1 .4 1 1V20c0 .6-.4 1-1 1A17 17 0 0 1 3 4c0-.6.4-1 1-1h3.5c.6 0 1 .4 1 1 0 1.3.2 2.5.6 3.6.1.3 0 .7-.2 1z"/></svg></span>
      <span>Call Us On :<br>555.010.2468</span>
    </div>
    <div class="footer-contact" style="left:639px">
      <span class="round-icon"><svg width="15" height="12" viewBox="0 0 20 14"><rect x="1" y="1" width="18" height="12" fill="none" stroke="#fff" stroke-width="1.6"/><path d="M1 1l9 7 9-7" fill="none" stroke="#fff" stroke-width="1.6"/></svg></span>
      <span>Email<br>info@rtmarlowbuild.com</span>
    </div>
    <div class="footer-rule"></div>
    <div class="copyright">Copyright &copy;2018 R.T.Marlow Construction Ltd. All Rights Reserved.</div>
    <div class="social" aria-label="Social links"><span></span><span></span><span></span><span></span></div>
  </footer>
</body>
</html>
```